Calvanto Group Real Estate Company business cards

New business card design, we are generally happy with the basic layout of the existing front of business card, (feel free to change) but require a head shot photo on the back side.

http://www.calvanto.com.au/

Attached logos, and existing business card

------------------------------

Target Market(s)

Real estate

Industry/Entity Type

Real Estate

Contact Information for Business Card

Standard size double sided

Font styles to use
Other font styles liked:
• Futura

Requirements
Must have
• Photo head shot on the back side
Nice to have
• yes
Should not have
• No

```html
<!DOCTYPE html>
<html lang="en">
<head>
<meta charset="utf-8">
<title>Calvanto Group – Business Card</title>
<link href="https://fonts.googleapis.com/css2?family=Open+Sans:wght@400;600&display=swap" rel="stylesheet">
<style>
  :root {
    --backdrop: #e9e6e2;
    --card: #ffffff;
    --ink-purple: #2b1a5c;
    --ink-text: #1e1e24;
    --accent-orange: #f7941d;
    --photo-light: #e8e8e8;
    --photo-dark: #8c96a8;
  }
  html, body {
    margin: 0;
    padding: 0;
    width: 1200px;
    height: 1000px;
    overflow: hidden;
    background: var(--backdrop);
    font-family: "Open Sans", Arial, sans-serif;
  }
  .stage { position: relative; width: 1200px; height: 1000px; }
  .card {
    position: absolute;
    left: 265px;
    width: 665px;
    height: 397px;
    background: var(--card);
    border-radius: 24px;
    box-shadow: 0 2px 8px rgba(0,0,0,0.15);
    overflow: hidden;
  }
  .card-front { top: 73px; }
  .card-back { top: 533px; }

  .brand {
    position: absolute;
    display: flex;
    align-items: center;
    gap: 12px;
  }
  .brand-mark {
    width: 22px;
    height: 22px;
    background: var(--accent-orange);
  }
  .brand-name {
    margin: 0;
    font-weight: 600;
    font-size: 42px;
    letter-spacing: -0.5px;
    color: var(--ink-purple);
    line-height: 1;
    white-space: nowrap;
  }
  .card-front .brand { left: 32px; top: 56px; }
  .card-back .brand { left: 0; right: 0; top: 278px; justify-content: center; }

  .accent-panel {
    position: absolute;
    left: 362px;
    top: 0;
    right: 0;
    bottom: 0;
    background: var(--accent-orange);
  }

  .holder-name {
    position: absolute; left: 33px; top: 188px; margin: 0;
    font-size: 21px; font-weight: 600; color: var(--ink-purple);
  }
  .holder-role {
    position: absolute; left: 33px; top: 216px; margin: 0;
    font-size: 15px; color: var(--ink-text);
  }
  .abn {
    position: absolute; left: 33px; top: 259px; margin: 0;
    font-size: 16px; color: var(--ink-text);
  }
  .contact-list {
    position: absolute; left: 33px; top: 296px;
    list-style: none; margin: 0; padding: 0;
    font-size: 16px; color: var(--ink-text);
  }
  .contact-list li { display: flex; align-items: center; height: 23.5px; }
  .contact-list svg { width: 14px; height: 14px; margin-right: 9px; fill: var(--ink-purple); }

  .headshot {
    position: absolute; left: 237px; top: 40px;
    width: 192px; height: 192px; border-radius: 50%;
    background: linear-gradient(180deg, var(--photo-light) 0%, #dcdde0 55%, var(--photo-dark) 100%);
  }
</style>
</head>
<body>
<div class="stage">
  <section class="card card-front">
    <div class="accent-panel"></div>
    <div class="brand">
      <p class="brand-name">Calvanto Group</p>
    </div>
    <p class="holder-name">Daniel Tran</p>
    <p class="holder-role">Director</p>
    <p class="abn">ABN: 12 345 678 901</p>
    <ul class="contact-list">
      <li>
        <svg viewBox="0 0 14 14" aria-hidden="true"><path d="M3.5 0h7a1 1 0 0 1 1 1v12a1 1 0 0 1-1 1h-7a1 1 0 0 1-1-1V1a1 1 0 0 1 1-1zm.5 1.5v9.5h6V1.5zm3 10.2a.7.7 0 1 0 0 1.4.7.7 0 0 0 0-1.4z"/></svg>
        0400 555 218
      </li>
      <li>
        <svg viewBox="0 0 14 14" aria-hidden="true"><path d="M0 3h14v8H0zm1 .8L7 8l6-4.2V4L7 8.2 1 4z"/></svg>
        daniel.tran@calvanto.com.au
      </li>
      <li>
        <svg viewBox="0 0 14 14" aria-hidden="true"><path d="M7 0a7 7 0 1 0 0 14A7 7 0 0 0 7 0zm0 1.3c.9 0 1.9 1.6 2.2 4.2H4.8C5.1 2.9 6.1 1.3 7 1.3zM4.7 6.8h4.6c0 2.8-1.2 5.9-2.3 5.9S4.7 9.6 4.7 6.8zM1.4 6.8h2c0 1.9.4 3.7 1 4.9a5.7 5.7 0 0 1-3-4.9zm9.2 0h2a5.7 5.7 0 0 1-3 4.9c.6-1.2 1-3 1-4.9zM1.5 5.5a5.7 5.7 0 0 1 3-3.8c-.5 1-.9 2.3-1 3.8zm9 0c-.1-1.5-.5-2.8-1-3.8a5.7 5.7 0 0 1 3 3.8z"/></svg>
        www.calvanto.com.au
      </li>
    </ul>
  </section>

  <section class="card card-back">
    <div class="headshot" role="img" aria-label="Head shot photo of the director in a dark suit and blue tie"></div>
    <div class="brand">
      <span class="brand-mark"></span>
      <p class="brand-name">Calvanto Group</p>
    </div>
  </section>
</div>
</body>
</html>
```